landscaping core flute signs

I need core flutes created with business name and a few extra dot points for putting on fences for job sites 120cm x 120cm approx.
I want our old ones information with the new L logo and colour palette

```html
<!DOCTYPE html>
<html lang="en">
<head>
<meta charset="utf-8">
<title>Stoneleaf Earthworks – Site Sign</title>
<link href="https://fonts.googleapis.com/css2?family=Montserrat:wght@500;600;700&display=swap" rel="stylesheet">
<style>
  :root {
    --backdrop: #e9e9e9;
    --sign: #ffffff;
    --ink: #222222;
    --ink-strong: #2b2b2b;
    --leaf: #5e8c55;
    --band: #0d0d0d;
    --on-leaf: #ffffff;
  }
  * { margin: 0; padding: 0; box-sizing: border-box; }
  html, body {
    width: 1200px; height: 829px; overflow: hidden;
    background: var(--backdrop);
    font-family: "Montserrat", Arial, sans-serif;
  }
  .sign {
    position: absolute; left: 210px; top: 24px;
    width: 780px; height: 780px;
    background: var(--sign); overflow: hidden;
  }
  .brand-mark {
    position: absolute; left: 302px; top: 56px;
    width: 176px; height: 176px; border-radius: 50%;
    background: var(--leaf);
  }
  .brand-name {
    position: absolute; left: 0; right: 0; top: 256px;
    text-align: center; font-weight: 700; font-size: 36px;
    letter-spacing: 1px; color: var(--ink);
  }
  .tagline {
    position: absolute; left: 0; right: 0; top: 334px;
    text-align: center; font-weight: 500; font-size: 14px;
    letter-spacing: 4px; color: var(--leaf);
  }
  .services {
    position: absolute; left: 196px; top: 390px; list-style: none;
  }
  .services li {
    display: flex; align-items: center; gap: 14px;
    height: 61px; font-weight: 500; font-size: 30px; color: var(--ink);
  }
  .services li::before {
    content: ""; width: 26px; height: 26px; border-radius: 50%;
    background: var(--leaf); flex: none;
  }
  .phone {
    position: absolute; left: 0; right: 0; top: 568px;
    text-align: center; font-weight: 700; font-size: 63px;
    letter-spacing: 1px; color: var(--ink-strong);
  }
  .email {
    position: absolute; left: 0; right: 0; top: 652px;
    text-align: center; font-weight: 600; font-size: 31px; color: var(--ink-strong);
  }
  .footer-wave { position: absolute; left: 0; top: 0; width: 780px; height: 780px; }
  .licence {
    position: absolute; right: 58px; top: 741px;
    font-weight: 700; font-size: 22px; line-height: 1; color: var(--on-leaf);
    word-spacing: 4px;
  }
</style>
</head>
<body>
  <main class="sign">
    <svg class="footer-wave" viewBox="0 0 796 796" aria-hidden="true">
      <path fill="var(--band)" d="M0,694 C150,766 300,778 440,758 C580,738 700,712 796,722 L796,736 C700,726 580,752 440,772 C300,792 150,782 0,712 Z"/>
      <path fill="var(--leaf)" d="M0,724 C150,792 300,790 440,778 C580,762 700,734 796,742 L796,796 L0,796 Z"/>
    </svg>

    <div class="brand-mark" aria-hidden="true"></div>
    <h1 class="brand-name">STONELEAF EARTHWORKS</h1>
    <p class="tagline">STRUCTURAL LANDSCAPING</p>

    <ul class="services">
      <li>Paving &amp; Concreting</li>
      <li>Fencing &amp; Retaining</li>
      <li>Desgin &amp; Construct</li>
    </ul>

    <p class="phone">0400 123 987</p>
    <p class="email">sam@stoneleafearthworks.com</p>
    <p class="licence">QBSA: 1234567</p>
  </main>
</body>
</html>
```